Podiatry clinic requires a modern revamp and editing of existing website.

I would like a fresh new look and updated information for my current business website. An easy to navigate site with prominent address and phone number for call to action. We are a podiatry clinic that focuses on general and sports podiatry.
I would like 4 pages; including Home page, About Us, Services & Contact.
www.brambleridgepodiatry.net

Target Market(s)

Active working professionals.

Industry/Entity Type

Medical

Coding

Coded - Design and coding required

Number of Pages Required

4 page

Font styles to use
Sans Serif

Colors
6b449b

Requirements
Must have
• A modern look with logo and active images; clean and uncluttered. Visible phone number and address for call to action.
• 4 pages - Home, About Us, Services, Contact.
• Home page - update address & service logos.
• About Us - update of personal information.
• Services - Revamp of existing page.
• Contact page to include Google map, email & phone number.
Nice to have
• Ability to add content easily; eg. a blog or adding video onto Home page.
• Link to Chatterly page.

```html
<!DOCTYPE html>
<html lang="en">
<head>
<meta charset="utf-8">
<title>Brambleridge Podiatry</title>
<link href="https://fonts.googleapis.com/css2?family=Raleway:wght@400;500;700;800&family=Open+Sans:wght@400;600;700&display=swap" rel="stylesheet">
<style>
:root{
  --purple:#4a2f96;
  --purple-dark:#452f91;
  --purple-bar:#5a3fb0;
  --green:#7cb518;
  --grey-bg:#f1f1f1;
  --text:#555;
  --heading-grey:#555;
  --white:#fff;
}
*{margin:0;padding:0;box-sizing:border-box}
html,body{width:1200px;height:2394px;overflow:hidden;background:var(--white)}
body{position:relative;font-family:"Open Sans",Arial,sans-serif;color:var(--text)}
.site-header{position:absolute;left:0;top:0;width:1200px;height:125px;background:var(--white);z-index:3}
.brand-disc{position:absolute;left:77px;top:-70px;width:200px;height:262px;border-radius:0 0 100px 100px;background:var(--white);z-index:4;display:flex;align-items:center;justify-content:center;padding:70px 18px 0}
.brand-name{font-family:"Raleway",sans-serif;font-weight:800;font-size:26px;line-height:1.15;color:var(--purple);text-align:center}
.main-nav a{position:absolute;top:44px;font-family:"Raleway",sans-serif;font-size:19px;color:#555;text-decoration:none}
.main-nav a.active{color:var(--purple)}
.header-phone{position:absolute;left:894px;top:33px;display:flex;align-items:center;gap:16px}
.header-phone .icon{width:50px;height:50px;border-radius:50%;background:var(--purple);display:flex;align-items:center;justify-content:center}
.header-phone span{font-weight:700;font-size:26px;color:var(--green)}
.hero{position:absolute;left:0;top:125px;width:1200px;height:572px;background:linear-gradient(180deg,#bcd6e3 0%,#d3e0e4 55%,#d8cbb4 78%,#8a735a 100%)}
.hero-runner{position:absolute;left:640px;top:0;width:300px;height:490px;background:radial-gradient(ellipse at center,#6d6a6a 0%,rgba(109,106,106,.4) 55%,rgba(109,106,106,0) 72%)}
.hero h1{position:absolute;left:80px;top:128px;font-family:"Raleway",sans-serif;font-weight:800;font-size:46px;line-height:78px;color:var(--purple)}
.hero p{position:absolute;left:80px;top:278px;width:370px;font-size:21px;line-height:31px;color:var(--purple)}
.btn{display:inline-block;background:var(--purple);color:var(--white);font-family:"Raleway",sans-serif;font-size:24px;border-radius:34px;text-align:center;text-decoration:none}
.hero .btn{position:absolute;left:77px;top:396px;width:229px;height:62px;line-height:62px}
.service-card{position:absolute;top:648px;width:322px;height:400px;background:var(--white);padding:10px}
.service-card .media{height:196px}
.service-card h2{margin-top:16px;font-family:"Raleway",sans-serif;font-weight:500;font-size:27px;color:var(--purple)}
.service-card p{margin-top:6px;font-size:15px;line-height:26px;color:var(--text)}
.read-more{position:absolute;left:12px;top:344px;font-family:"Raleway",sans-serif;font-weight:700;font-size:19px;color:var(--purple);text-decoration:none}
.play{width:56px;height:56px;border-radius:50%;background:rgba(255,255,255,.85);display:flex;align-items:center;justify-content:center}
.divider{position:absolute;left:270px;top:1070px;width:660px;height:16px;background:radial-gradient(ellipse at top,rgba(0,0,0,.12),rgba(0,0,0,0) 70%)}
.welcome h2{position:absolute;left:0;top:1140px;width:1200px;text-align:center;font-family:"Raleway",sans-serif;font-weight:400;font-size:43px;color:var(--heading-grey)}
.welcome h2 b,.news h2 b{font-weight:500;color:var(--purple)}
.welcome p{position:absolute;left:210px;top:1210px;width:780px;text-align:center;font-size:16px;line-height:26px}
.welcome .btn{position:absolute;left:504px;top:1285px;width:190px;height:51px;line-height:51px;font-size:22px}
.news{position:absolute;left:0;top:1393px;width:1200px;height:501px;background:var(--grey-bg)}
.news h2{position:absolute;left:0;top:58px;width:1200px;text-align:center;font-family:"Raleway",sans-serif;font-weight:400;font-size:43px;color:var(--heading-grey)}
.news-item{position:absolute;top:122px;width:235px}
.news-item .media{height:145px}
.news-item h3{margin-top:14px;font-family:"Raleway",sans-serif;font-weight:500;font-size:18px;line-height:25px;color:var(--purple)}
.news-item time{display:flex;align-items:center;gap:7px;margin-top:4px;font-size:14px;color:#999}
.news-item p{margin-top:6px;font-size:15.5px;line-height:25px}
.partners .badge{position:absolute;top:1952px;height:72px;border-radius:8px;background:#e4e4ee}
.site-footer{position:absolute;left:0;top:2084px;width:1200px;height:257px;background:var(--purple-dark);color:var(--white)}
.footer-brand{position:absolute;left:83px;top:60px;font-family:"Raleway",sans-serif;font-weight:800;font-size:30px;line-height:1.2;color:#c8bde6}
.footer-col{position:absolute;top:44px}
.footer-col h4{font-family:"Raleway",sans-serif;font-weight:400;font-size:21px;margin-bottom:16px;color:#e9e4f6}
.footer-col li{list-style:none;display:flex;align-items:flex-start;gap:12px;font-size:17px;line-height:24px;margin-bottom:13px}
.footer-col li.bold{font-weight:700}
.footer-col li svg{flex:none;margin-top:4px}
.social li{align-items:center;gap:14px;margin-bottom:22px}
.social .ring{width:46px;height:46px;border:2px solid var(--white);border-radius:50%}
.copyright{position:absolute;left:0;top:2341px;width:1200px;height:53px;background:var(--purple-bar);color:#e9e4f6;text-align:center;line-height:53px;font-size:15.5px}
</style>
</head>
<body>

<header class="site-header">
  <nav class="main-nav">
    <a class="active" style="left:412px">HOME</a>
    <a style="left:507px">ABOUT</a>
    <a style="left:616px">SERVICES</a>
    <a style="left:748px">CONTACT</a>
  </nav>
  <div class="header-phone">
    <div class="icon"><svg width="24" height="24" viewBox="0 0 24 24"><path fill="#fff" d="M6.6 10.8a15.1 15.1 0 0 0 6.6 6.6l2.2-2.2c.3-.3.7-.4 1-.2 1.1.4 2.3.6 3.6.6.6 0 1 .4 1 1V20c0 .6-.4 1-1 1A17 17 0 0 1 3 4c0-.6.4-1 1-1h3.5c.6 0 1 .4 1 1 0 1.3.2 2.5.6 3.6.1.3 0 .7-.2 1z"/></svg></div>
    <span>1300 555 274</span>
  </div>
</header>
<div class="brand-disc"><div class="brand-name">Brambleridge Podiatry</div></div>

<section class="hero">
  <div class="hero-runner" role="img" aria-label="Photo of a woman running on a sunny beach boardwalk"></div>
  <h1>QUALIFIED HEALTH<br>PROFESSIONALS</h1>
  <p>Various foot conditions, including Sports Injuries, Orthotic Therapy &amp; Nail Surgery</p>
  <a class="btn">CONTACT US</a>
</section>

<section class="services">
  <article class="service-card" style="left:77px">
    <div class="media" role="img" aria-label="Photo of a podiatrist examining a patient's foot" style="background:linear-gradient(135deg,#eef1f3,#d8c3b4)"></div>
    <h2>General Treatment</h2>
    <p>Nails, Corns, Callus, Warts, Skin Disorders, Heel pain / Heel Spurs / Arch pain - plantar Fasciitis</p>
    <a class="read-more">READ MORE »</a>
  </article>
  <article class="service-card" style="left:439px">
    <div class="media" role="img" aria-label="Photo of a nail treatment on a toe with a podiatry tool" style="background:linear-gradient(135deg,#f4ece8,#e7b9a8)"></div>
    <h2>Specialised Treatments</h2>
    <p>Diabetic Management, Nail Surgery, Biomechanical Assessment, Gait Analysis, Orthotic Therapy</p>
    <a class="read-more">READ MORE »</a>
  </article>
  <article class="service-card" style="left:800px">
    <div class="media" role="img" aria-label="Video still of a podiatrist in a clinic" style="background:linear-gradient(135deg,#9aa3ad,#d9dde2);display:flex;align-items:center;justify-content:center">
      <span class="play"><svg width="20" height="22" viewBox="0 0 20 22"><path d="M3 1l16 10L3 21z" fill="#4a2f96"/></svg></span>
    </div>
    <h2>ABOUT PODIATRISTS</h2>
    <p>Our podiatrists are fully qualified health professionals who are able to diagnose, treat, manage or help to prevent all...</p>
    <a class="read-more">READ MORE »</a>
  </article>
</section>

<div class="divider"></div>

<section class="welcome">
  <h2>WELCOME TO <b>BRAMBLERIDGE PODIATRY</b></h2>
  <p>Brambleridge Podiatry is a Podiatry clinic in the heart of Melbourne CBD. We are located between Harlow &amp; Denby Streets in the Harlow Business Centre / Linden Court Complex.</p>
  <a class="btn">READ MORE</a>
</section>

<section class="news">
  <h2>LATEST <b>NEWS</b></h2>
  <article class="news-item" style="left:77px">
    <div class="media" role="img" aria-label="Photo of a practitioner treating a patient's leg" style="background:linear-gradient(135deg,#e9e6e1,#b7a99a)"></div>
    <h3>Lorem Ipsum is dummy text and simply printing.</h3>
    <time><svg width="13" height="13" viewBox="0 0 13 13"><rect x="1" y="2" width="11" height="10" fill="none" stroke="#999"/><path d="M1 5h11" stroke="#999"/></svg>01 August 2016</time>
    <p>Lorem Ipsum is simply dummy text of the printing and type setting industry.</p>
  </article>
  <article class="news-item" style="left:348px">
    <div class="media" role="img" aria-label="Photo of bare feet walking on wet sand" style="background:linear-gradient(180deg,#8d8d93,#5e5a55)"></div>
    <h3>Lorem Ipsum is dummy text and simply printing.</h3>
    <time><svg width="13" height="13" viewBox="0 0 13 13"><rect x="1" y="2" width="11" height="10" fill="none" stroke="#999"/><path d="M1 5h11" stroke="#999"/></svg>01 August 2016</time>
    <p>Lorem Ipsum is simply dummy text of the printing and type setting industry.</p>
  </article>
  <article class="news-item" style="left:619px">
    <div class="media" role="img" aria-label="Illustration of a foot with the heel area highlighted" style="background:radial-gradient(circle at 45% 55%,#e9a0a0,#c8cfe0 40%,#fff 70%)"></div>
    <h3>Lorem Ipsum is dummy text and simply printing.</h3>
    <time><svg width="13" height="13" viewBox="0 0 13 13"><rect x="1" y="2" width="11" height="10" fill="none" stroke="#999"/><path d="M1 5h11" stroke="#999"/></svg>01 August 2016</time>
    <p>Lorem Ipsum is simply dummy text of the printing and type setting industry.</p>
  </article>
  <article class="news-item" style="left:889px">
    <div class="media" role="img" aria-label="Photo of a practitioner consulting with a patient" style="background:linear-gradient(135deg,#efe9e4,#d9a9a6)"></div>
    <h3>Lorem Ipsum is dummy text and simply printing.</h3>
    <time><svg width="13" height="13" viewBox="0 0 13 13"><rect x="1" y="2" width="11" height="10" fill="none" stroke="#999"/><path d="M1 5h11" stroke="#999"/></svg>01 August 2016</time>
    <p>Lorem Ipsum is simply dummy text of the printing and type setting industry.</p>
  </article>
</section>

<section class="partners">
  <div class="badge" style="left:83px;width:220px"></div>
  <div class="badge" style="left:348px;width:235px"></div>
  <div class="badge" style="left:626px;width:218px"></div>
  <div class="badge" style="left:900px;width:218px"></div>
</section>

<footer class="site-footer">
  <div class="footer-brand">Brambleridge<br>Podiatry</div>
  <div class="footer-col" style="left:350px">
    <h4>Useful Links</h4>
    <ul>
      <li>→ Home</li><li>→ About</li><li>→ Services</li><li>→ Contact</li>
    </ul>
  </div>
  <div class="footer-col" style="left:621px;width:240px">
    <h4>Get In Touch</h4>
    <ul>
      <li><svg width="14" height="20" viewBox="0 0 14 20"><path fill="#fff" d="M7 0a7 7 0 0 0-7 7c0 5 7 13 7 13s7-8 7-13a7 7 0 0 0-7-7zm0 10a3 3 0 1 1 0-6 3 3 0 0 1 0 6z"/></svg><span>Suite 210 / 88 Harlow Street Melbourne 3000</span></li>
      <li class="bold"><svg width="18" height="18" viewBox="0 0 24 24"><path fill="#fff" d="M6.6 10.8a15.1 15.1 0 0 0 6.6 6.6l2.2-2.2c.3-.3.7-.4 1-.2 1.1.4 2.3.6 3.6.6.6 0 1 .4 1 1V20c0 .6-.4 1-1 1A17 17 0 0 1 3 4c0-.6.4-1 1-1h3.5c.6 0 1 .4 1 1 0 1.3.2 2.5.6 3.6.1.3 0 .7-.2 1z"/></svg><span>1300 555 274</span></li>
      <li><svg width="18" height="14" viewBox="0 0 18 14"><rect x="1" y="1" width="16" height="12" fill="none" stroke="#fff" stroke-width="1.6"/><path d="M1 1l8 7 8-7" fill="none" stroke="#fff" stroke-width="1.6"/></svg><span style="word-break:break-all">info@brambleridgepodiatry.net</span></li>
    </ul>
  </div>
  <div class="footer-col social" style="left:891px">
    <h4>Follow Us</h4>
    <ul>
      <li><span class="ring"></span>Chatterly</li>
      <li><span class="ring"></span>Postwave</li>
    </ul>
  </div>
</footer>
<div class="copyright">© Brambleridge Podiatry- 2016. All Rights Reserved.</div>

</body>
</html>
```